20 year old business card needs re-design

We need to redesign our corporate business card look. We need something that appears more modern, eye catchy but professional.

Target Market(s)

manufacturing industry

Industry/Entity Type

Manufacturer

Contact Information for Business Card

One side can have the logo. Other side can have contact information.

Font styles to use
Serif

Colors
3277b5
33b8a4
ffffff

Requirements
Must have
• Eye catchy - need to standout from the crowd. company logo cannot change. Full name, job title, phone number and email address.
Should not have
• Fax, business address is not necessary.

```html
<!DOCTYPE html>
<html lang="en">
<head>
<meta charset="utf-8">
<title>Verenta Industrial – Business Card</title>
<link rel="stylesheet" href="https://fonts.googleapis.com/css2?family=Lato:wght@400;700;900&display=swap">
<style>
  :root {
    --bg: #2b2b2b;
    --card-dark: #151616;
    --card-light: #ffffff;
    --brand-blue: #2f5fb4;
    --text-grey: #6b6b6b;
    --rule-grey: #9a9a9a;
    --white: #ffffff;
  }
  * { box-sizing: border-box; margin: 0; padding: 0; }
  html, body { width: 1200px; height: 1031px; overflow: hidden; }
  body {
    background: var(--bg);
    font-family: "Lato", sans-serif;
    position: relative;
  }
  .card {
    position: absolute;
    width: 560px;
    height: 320px;
    border-radius: 16px;
    box-shadow: 0 14px 40px rgba(0,0,0,.45);
    overflow: hidden;
  }
  /* Front */
  .card-front {
    left: 90px; top: 120px;
    background: repeating-linear-gradient(0deg, var(--card-dark) 0 7px, #1b1c1c 7px 8px);
    display: flex; flex-direction: column; align-items: center; justify-content: center;
    gap: 26px;
  }
  .front-brand {
    display: flex; align-items: center; gap: 14px;
    color: var(--white); font-weight: 900; font-size: 46px; letter-spacing: -0.5px;
  }
  .brand-square { width: 26px; height: 26px; background: var(--white); }
  .front-web {
    color: var(--white); font-size: 20px; letter-spacing: 5px; font-weight: 400;
  }
  .front-web .accent { color: var(--brand-blue); }

  /* Back */
  .card-back {
    left: 550px; top: 560px;
    background: repeating-linear-gradient(0deg, var(--card-light) 0 7px, #f4f4f4 7px 8px);
    padding: 34px 34px 0 34px;
  }
  .back-top { display: flex; justify-content: space-between; }
  .back-brand { padding-top: 92px; }
  .back-brand-name {
    display: flex; align-items: center; gap: 9px;
    color: var(--brand-blue); font-weight: 900; font-size: 28px; letter-spacing: -0.3px;
  }
  .back-brand-name .brand-square { width: 16px; height: 16px; background: var(--brand-blue); }
  .cert { color: var(--text-grey); font-size: 11.5px; margin-top: 8px; }
  .person { width: 240px; }
  .person-name { color: var(--brand-blue); font-weight: 700; font-size: 22px; }
  .person-title { color: var(--text-grey); font-size: 13px; margin-top: 2px; }
  .social { display: flex; gap: 6px; margin: 10px 0 10px; }
  .social span { width: 14px; height: 14px; border-radius: 50%; background: var(--brand-blue); }
  .contact { list-style: none; }
  .contact li {
    display: flex; align-items: center; gap: 8px;
    color: var(--text-grey); font-size: 12.5px; line-height: 19px;
  }
  .contact li.web { color: var(--brand-blue); font-weight: 700; }
  .contact svg { width: 12px; height: 12px; flex: none; }
  .tagline {
    position: absolute; left: 34px; right: 34px; bottom: 22px;
    border-top: 1px solid var(--rule-grey);
    padding-top: 8px;
    color: var(--brand-blue); font-weight: 700; font-size: 14.5px;
  }
</style>
</head>
<body>
  <section class="card card-front" aria-label="Business card front">
    <div class="front-brand"><span class="brand-square"></span>Verenta Industrial</div>
    <div class="front-web">VerentaIndustrial<span class="accent">.com</span></div>
  </section>

  <section class="card card-back" aria-label="Business card back">
    <div class="back-top">
      <div class="back-brand">
        <div class="back-brand-name"><span class="brand-square"></span>Verenta Industrial</div>
        <p class="cert">TS16949 &amp; ISO9001 Certified Facilities</p>
      </div>
      <div class="person">
        <h1 class="person-name">Daniel Reyes</h1>
        <p class="person-title">Senior Project Manager</p>
        <div class="social" aria-label="Social profiles"><span></span><span></span><span></span></div>
        <ul class="contact">
          <li><svg viewBox="0 0 12 12"><rect x="1" y="1" width="10" height="10" fill="none" stroke="#6b6b6b" stroke-width="1.2"/></svg>555-014-2200</li>
          <li><svg viewBox="0 0 12 12"><circle cx="6" cy="6" r="5" fill="none" stroke="#2f5fb4" stroke-width="1.4"/><path d="M4 4 l1 2 l3 2" stroke="#2f5fb4" stroke-width="1.4" fill="none"/></svg>555-014-2201 x 118</li>
          <li><svg viewBox="0 0 12 12"><path d="M1 3 h10 v7 h-10 z M1 3 l5 4 l5 -4" fill="none" stroke="#2f5fb4" stroke-width="1.3"/></svg>daniel@verentaindustrial.com</li>
          <li class="web"><svg viewBox="0 0 12 12"><circle cx="6" cy="6" r="5" fill="none" stroke="#2f5fb4" stroke-width="1.3"/><path d="M1 6 h10 M6 1 c-3 3 -3 7 0 10 c3 -3 3 -7 0 -10" fill="none" stroke="#2f5fb4" stroke-width="1"/></svg>VerentaIndustrial.com</li>
        </ul>
      </div>
    </div>
    <p class="tagline">International manufacturing solutions for OEM customers in North America</p>
  </section>
</body>
</html>
```